WE ARE BRIGHT SPARROW, building a full website with ecommerce

requirements:
CODED FOR SITEQUILL
ONLINE STORE FUNCTION WITH E-COMMERCE USING TRADEBLOOM
PAGEWAVE AND PICTOLANE LINKS

I need a website design for my organization, WE ARE BRIGHT SPARROW, a global empowerment movement elevating woman, and the world. The site's home page should reflect our mission, to empower women. It should have a strong, empowering feel, with minimalistic design.
Please see www.lunavelto.com and http://www.corvenhal.co/ for an inspiration on layout and feel.

**PLEASE SEE ATTACHMENT "LOGO MOCK UP" FOR LOGO. THIS IS NOT THE FINAL VECTOR FILE, BUT THIS LOOKS THE SAME AS THE FINAL LOGO.

HOME PAGE:
The first section of the home page should include a background image with our logo center.

You should include the following links to pages at the top right of the page:
MISSION
MANTRA
ARMOR
MEET BS (I would like "bs" to be our logo)
pagewave and pictolane links

As you scroll down the page, you should see the following sections, which correlate to the links to pages as written above. **SEE ATTACHED SKETCH "HOMEPAGE LAYOUT IDEA" FOR REFERENCE**

WHO WE ARE (correlates to the link Mission)

OUR MANTRA (correlates to the link Mantra)

OUR ARMOR (correlates to the link The Shirt)
(This is where we will sell a shirt (and other apparel) and need the e-commerce function)

MEET BRIGHT SPARROWS (correlates to the link Meet BS)

SHOW OFF YOUR SUPER POWERS (correlates to the pagewave and pictolane)

FEATURED BRIGHT SPARROW (no link on top right of page)

On the homepage, for each of the above sections, as you scroll down there should be an image, either in the background or framed, next to the title (WHO WE ARE, for example), as well as one sentence of small text explaining the title. The title (WHO WE ARE) and the one sentence should link to a page (ie WHO WE ARE + the one sentence links to the MISSION page). ** SEE ATTACHED SKETCH "HOMEPAGE SECTION IDEAS" FOR REFERENCE**

**PLEASE SEE ATTACHMENT "WEBSITE TITLE IDEAS" FOR A STARTING PLACE OF THE LOOK. These don't have to be exact, but they give you an idea of what I'm looking for.

**FONTS TYPOLD EXTRA BOLD AND TYPOLD BOOK 500 (WHICH SHOULD BE BOLDED MANUALLY) ARE ATTACHED**

Target Market(s)

Women, mainly in US

Industry/Entity Type

Social

Coding

Coded - Design and coding required

Number of Pages Required

5+ page

Font styles to use
Other font styles liked:
• Typol Extra Bold

Requirements
Must have
• CODED FOR SITEQUILL
• ONLINE STORE FUNCTION WITH E-COMMERCE USING TRADEBLOOM
• PAGEWAVE AND PICTOLANE LINKS
• Typold Extra Bold and Typold Book 500, attached
• please see description for all requirements
Nice to have
• please see description for all ideas
Should not have

```html
<!DOCTYPE html>
<html lang="en">
<head>
<meta charset="utf-8">
<title>We Are Bright Sparrow</title>
<link href="https://fonts.googleapis.com/css2?family=Montserrat:wght@400;500;600;700;800;900&display=swap" rel="stylesheet">
<style>
:root{
  --ink:#111111;
  --text:#333333;
  --muted:#777777;
  --teal:#5bd6c4;
  --teal-dark:#3fc3b0;
  --panel:#f4f4f4;
  --line:#dcdcdc;
  --white:#ffffff;
  --footer:#0d0d0d;
  --head:"Montserrat",Arial,sans-serif;
}
*{margin:0;padding:0;box-sizing:border-box}
html,body{width:1200px;height:3982px;overflow:hidden}
body{position:relative;background:var(--white);font-family:var(--head);color:var(--text)}
.abs{position:absolute}

/* brand lockup */
.brand{display:flex;align-items:center;gap:12px;color:var(--ink)}
.brand-mark{width:26px;height:26px;border:5px solid currentColor;flex:none}
.brand-name{font-weight:800;font-size:17px;line-height:16px;letter-spacing:.5px;text-transform:uppercase}

/* header */
.site-header{left:0;top:0;width:1200px;height:88px;background:var(--white)}
.site-header .brand{position:absolute;left:98px;top:16px}
.main-nav{position:absolute;left:560px;top:33px;display:flex;gap:38px;font-size:15px;font-weight:500;color:var(--ink);letter-spacing:.3px}
.social-top{position:absolute;left:1010px;top:33px;display:flex;gap:14px;font-size:11px;font-weight:700;color:var(--ink)}

/* hero */
.hero{left:0;top:88px;width:1200px;height:478px;background:radial-gradient(circle at 15% 15%,#b8b0c6 0,#5a4f5f 10%,#2a2228 35%,#1b1618 70%),#1b1618}
.hero-photo{position:absolute;inset:0;background:linear-gradient(90deg,rgba(60,50,60,.2),rgba(20,15,18,.2) 55%,rgba(70,55,50,.55) 80%,rgba(30,25,25,.2))}
.hero-mark{position:absolute;left:575px;top:100px;width:50px;height:50px;border:7px solid var(--white)}
.hero-title{position:absolute;left:0;width:1200px;top:200px;text-align:center;color:var(--white);font-weight:700;font-size:47px;letter-spacing:1px}
.hero-sub{position:absolute;left:0;width:1200px;top:265px;text-align:center;color:var(--white);font-weight:400;font-size:19px;letter-spacing:1.5px}
.signup{position:absolute;left:305px;top:323px;width:590px;height:56px;display:flex}
.signup-field{flex:1;background:var(--white);display:flex;align-items:center;padding-left:22px;gap:14px;font-size:11px;color:#999;letter-spacing:1px}
.signup-field svg{flex:none}
.signup-btn{width:150px;background:var(--teal);color:var(--white);font-weight:700;font-size:15px;display:flex;align-items:center;justify-content:center;letter-spacing:.5px}

/* intro */
.intro{left:0;top:628px;width:1200px;text-align:center;font-size:25px;line-height:44px;letter-spacing:1.5px;color:var(--ink)}
.intro strong{font-weight:800}
.fly{left:505px;top:757px;display:flex;align-items:center;gap:14px;color:var(--ink)}
.fly .brand-mark{width:58px;height:58px;border-width:8px;transform:rotate(45deg)}
.fly-text{font-weight:900;font-size:42px;line-height:38px;letter-spacing:.5px}

/* feature rows */
.feature{left:0;width:1200px}
.feature.grey{background:var(--panel)}
.feature-photo{position:absolute;top:0;height:100%}
.section-title{position:absolute;display:flex;align-items:center;gap:18px;color:var(--ink)}
.section-title .brand-mark{width:54px;height:54px;border-width:8px;transform:rotate(45deg)}
.section-title h2{font-weight:900;font-size:35px;line-height:32px;text-transform:uppercase}
.feature p{position:absolute;width:470px;font-size:13px;line-height:25px;color:var(--muted)}

/* armor */
.armor-title{left:475px;top:2200px}
.product{position:absolute;top:2344px;width:300px}
.product-frame{height:274px;border:2px solid var(--line);display:flex;align-items:center;justify-content:center}
.product-shot{width:230px;height:220px;border-radius:8px}
.product-name{margin-top:32px;text-align:center;font-size:21px;color:var(--text);letter-spacing:.3px}
.product-price{margin-top:12px;text-align:center;font-size:14px;color:var(--text)}
.buy-btn{display:block;margin:18px auto 0;width:142px;height:48px;border:2px solid var(--line);color:var(--teal-dark);font-size:13px;font-weight:600;letter-spacing:.5px;text-align:center;line-height:44px}

/* social band */
.powers{left:0;top:2870px;width:1200px;height:159px;background:var(--teal)}
.powers-title{position:absolute;left:340px;top:38px;display:flex;align-items:center;gap:22px;color:var(--white)}
.powers-title .brand-mark{width:62px;height:62px;border-width:9px;transform:rotate(45deg);border-color:var(--white)}
.powers-title .small{font-weight:800;font-size:17px;letter-spacing:1px;line-height:18px}
.powers-title .big{font-weight:900;font-size:38px;line-height:34px}
.social-ring{position:absolute;top:45px;width:70px;height:70px;border:2px solid var(--white);border-radius:50%;color:var(--white);font-size:9px;font-weight:700;display:flex;align-items:center;justify-content:center;letter-spacing:.3px}

/* featured */
.featured-title{left:485px;top:3118px}
.featured-title h2{font-size:29px;line-height:37px}
.person{position:absolute;top:3260px;width:214px;text-align:center}
.person-photo{width:214px;height:214px;border-radius:50%;border:6px solid #ececec}
.person-name{margin-top:30px;font-weight:700;font-size:17px;color:var(--ink);letter-spacing:.5px}
.person-role{margin-top:8px;font-size:14px;color:var(--muted)}

/* footer */
.site-footer{left:0;top:3632px;width:1200px;height:350px;background:var(--footer);color:var(--white)}
.footer-mark{position:absolute;left:572px;top:82px;width:56px;height:56px;border:8px solid var(--white);transform:rotate(45deg)}
.footer-name{position:absolute;left:0;width:1200px;top:160px;text-align:center;font-weight:800;font-size:14px;letter-spacing:2px}
.footer-nav{position:absolute;left:0;width:1200px;top:184px;display:flex;justify-content:center;gap:44px;font-size:14px;font-weight:600;letter-spacing:.5px}
.copyright{position:absolute;left:0;width:1200px;top:228px;text-align:center;font-size:13px;color:#cfcfcf}
.footer-social{position:absolute;left:0;width:1200px;top:272px;display:flex;justify-content:center;gap:18px;font-size:11px;font-weight:700}
</style>
</head>
<body>

<header class="abs site-header">
  <div class="brand">
    <span class="brand-mark"></span>
    <span class="brand-name">We Are<br>Bright<br>Sparrow</span>
  </div>
  <nav class="main-nav">
    <span>MISSION</span><span>MANTRA</span><span>MEET BS</span><span>THE SHIRT</span>
  </nav>
  <div class="social-top"><span>PAGEWAVE</span><span>PICTOLANE</span></div>
</header>

<section class="abs hero">
  <div class="hero-photo" role="img" aria-label="Photo of a speaker addressing a crowded audience under stage lights"></div>
  <span class="hero-mark"></span>
  <h1 class="hero-title">WE ARE BRIGHT SPARROW</h1>
  <p class="hero-sub">AND WE WILL CONQUER THE WORLD</p>
  <form class="signup">
    <div class="signup-field">
      <svg width="14" height="10" viewBox="0 0 14 10"><rect x=".5" y=".5" width="13" height="9" fill="none" stroke="#999"/><path d="M.5 .5L7 5.5 13.5 .5" fill="none" stroke="#999"/></svg>
      EMAIL ADDRESS
    </div>
    <div class="signup-btn">LET'S FLY</div>
  </form>
</section>

<p class="abs intro"><strong>WE ARE BRIGHT SPARROW</strong> IS A GLOBAL EMPOWERMENT<br>MOVEMENT ELEVATING WOMEN... AND THE WORLD.</p>

<div class="abs fly">
  <span class="brand-mark"></span>
  <span class="fly-text">LET'S<br>FLY</span>
</div>

<!-- Who we are -->
<section class="abs feature grey" style="top:927px;height:401px">
  <div class="feature-photo" style="left:584px;width:616px;background:linear-gradient(120deg,#dfe6ea,#9aa9b4 45%,#4d5a6e 70%,#d9dfe3);clip-path:polygon(66px 0,616px 0,616px 401px,0 401px)" role="img" aria-label="Photo of two women talking at a meeting table"></div>
  <svg class="abs" style="left:584px;top:0" width="70" height="401"><line x1="66" y1="0" x2="0" y2="401" stroke="var(--teal)" stroke-width="4"/></svg>
  <div class="section-title" style="left:98px;top:108px">
    <span class="brand-mark"></span><h2>Who<br>We<br>Are</h2>
  </div>
  <p style="left:178px;top:222px">Nemo enim ipsam voluptatem quia voluptas sit aspernatur aut odit aut fugit, sed quia consequuntur magni dolores eos qui ratione voluptatem sequi nesciunt.</p>
</section>

<!-- Our mantra -->
<section class="abs feature" style="top:1328px;height:400px">
  <div class="feature-photo" style="left:0;width:624px;background:linear-gradient(160deg,#e8e5e1,#b7aea6 40%,#6f6a6c 70%,#3f4a5c);clip-path:polygon(0 0,544px 0,624px 400px,0 400px)" role="img" aria-label="Photo of an audience raising hands to a presenter"></div>
  <svg class="abs" style="left:540px;top:0" width="90" height="400"><line x1="4" y1="0" x2="84" y2="400" stroke="var(--teal)" stroke-width="4"/></svg>
  <div class="section-title" style="left:637px;top:110px">
    <span class="brand-mark"></span><h2>Our<br>Mantra</h2>
  </div>
  <p style="left:716px;top:192px">Nemo enim ipsam voluptatem quia voluptas sit aspernatur aut odit aut fugit, sed quia consequuntur magni dolores eos qui ratione voluptatem sequi nesciunt.</p>
</section>

<!-- Meet bright sparrows -->
<section class="abs feature grey" style="top:1728px;height:388px">
  <div class="feature-photo" style="left:584px;width:616px;background:linear-gradient(110deg,#6a7c93,#c5cfd9 40%,#e4e2e0 55%,#58667a 80%,#2d3645);clip-path:polygon(66px 0,616px 0,616px 388px,0 388px)" role="img" aria-label="Photo of a smiling woman presenting on stage in front of a screen"></div>
  <svg class="abs" style="left:584px;top:0" width="70" height="388"><line x1="66" y1="0" x2="0" y2="388" stroke="var(--teal)" stroke-width="4"/></svg>
  <div class="section-title" style="left:98px;top:100px">
    <span class="brand-mark"></span><h2 style="font-size:31px;line-height:30px">Meet<br>Bright<br>Sparrows</h2>
  </div>
  <p style="left:178px;top:204px">Nemo enim ipsam voluptatem quia voluptas sit aspernatur aut odit aut fugit, sed quia consequuntur magni dolores eos qui ratione voluptatem sequi nesciunt.</p>
</section>

<!-- Our armor -->
<div class="abs section-title armor-title">
  <span class="brand-mark"></span><h2>Our<br>Armor</h2>
</div>

<article class="product" style="left:98px">
  <div class="product-frame"><div class="product-shot" style="background:#a9a9a9" role="img" aria-label="Grey t-shirt with the movement emblem"></div></div>
  <p class="product-name">Finibus Bonoruet Malo</p>
  <p class="product-price">$27.00</p>
  <span class="buy-btn">BUY NOW!</span>
</article>
<article class="product" style="left:449px">
  <div class="product-frame"><div class="product-shot" style="background:#1d1d1d" role="img" aria-label="Black t-shirt with the movement emblem"></div></div>
  <p class="product-name">Finibus Bonoruet Malo</p>
  <p class="product-price">$27.00</p>
  <span class="buy-btn">BUY NOW!</span>
</article>
<article class="product" style="left:799px">
  <div class="product-frame"><div class="product-shot" style="background:#f1f1f1;border:1px solid #e4e4e4" role="img" aria-label="White t-shirt with the movement emblem"></div></div>
  <p class="product-name">Finibus Bonoruet Malo</p>
  <p class="product-price">$27.00</p>
  <span class="buy-btn">BUY NOW!</span>
</article>

<!-- Show off your super powers -->
<section class="abs powers">
  <div class="powers-title">
    <span class="brand-mark"></span>
    <div><div class="small">SHOW OFF YOUR</div><div class="big">SUPER<br>POWERS</div></div>
  </div>
  <span class="social-ring" style="left:688px">PAGEWAVE</span>
  <span class="social-ring" style="left:796px">PICTOLANE</span>
</section>

<!-- Featured -->
<div class="abs section-title featured-title">
  <span class="brand-mark"></span><h2>Featured<br>Bright<br>Sparrow</h2>
</div>

<div class="person" style="left:100px">
  <div class="person-photo" style="background:radial-gradient(circle at 50% 45%,#d9c2b0,#b9a79a 55%,#e9e6e3)" role="img" aria-label="Portrait of Katie"></div>
  <p class="person-name">KATIE</p><p class="person-role">Finibus Bonorumet</p>
</div>
<div class="person" style="left:360px">
  <div class="person-photo" style="background:radial-gradient(circle at 50% 45%,#dcc4b4,#a99688 55%,#ebe7e4)" role="img" aria-label="Portrait of Clara"></div>
  <p class="person-name">CLARA</p><p class="person-role">Finibus Bonorumet</p>
</div>
<div class="person" style="left:623px">
  <div class="person-photo" style="background:radial-gradient(circle at 50% 45%,#e6cfb4,#d8bf8f 50%,#f0eeec)" role="img" aria-label="Portrait of Agnus"></div>
  <p class="person-name">AGNUS</p><p class="person-role">Finibus Bonorumet</p>
</div>
<div class="person" style="left:886px">
  <div class="person-photo" style="background:radial-gradient(circle at 50% 45%,#d6bba7,#5a4e4a 55%,#e6e6e6)" role="img" aria-label="Portrait of Susan"></div>
  <p class="person-name">SUSAN</p><p class="person-role">Finibus Bonorumet</p>
</div>

<footer class="abs site-footer">
  <span class="footer-mark"></span>
  <nav class="footer-nav" style="top:184px">
    <span>MISSION</span><span>MANTRA</span><span>MEET BS</span><span>THE SHIRT</span>
  </nav>
  <p class="copyright">Copyright © 2017, We Are Bright Sparrow. All right reserved.</p>
  <div class="footer-social"><span>PAGEWAVE</span><span>PICTOLANE</span></div>
</footer>

</body>
</html>
```